Meridale Bed Company Needs Business Card

Looking for a very nice looking business card. Creative but not extravagant. We sell beds and pillows across the U.S. and need something professional but catchy. I have attached the logo.

Name : Devin Holt
Title : President
Phone : (800) 471-2960
Email: sleep@quilmora.com
Website: www.quilmora.com

Can be single-sided or double-sided
horizontal or vertical

Can use Blues/Greys

Target Market(s)

Mass Market

Industry/Entity Type

Retail

Contact Information for Business Card

Name : Devin Holt
Title : President
Phone : (800) 471-2960
Email: sleep@quilmora.com
Website: www.quilmora.com

Requirements
Must have
• Clean, Modern, Smooth
• Can use Blues/Greys
• On the other side without the information - have something simple like www.quilmora.com or our logo
Nice to have
• Surprise me
Should not have
• Nothing crazy, nothing cluttered

```html
<!DOCTYPE html>
<html lang="en">
<head>
<meta charset="utf-8">
<title>Quilmora Business Card</title>
<link rel="stylesheet" href="https://fonts.googleapis.com/css2?family=Arimo:wght@400;700&display=swap">
<style>
  :root {
    --page-bg: #e6e8eb;
    --card-white: #ffffff;
    --brand-blue: #2fa3d8;
    --brand-blue-deep: #1f8bc2;
    --brand-blue-light: #45b4e6;
    --band-grey: #6f7173;
    --band-grey-light: #a9abad;
    --text-grey: #555759;
    --text-white: #ffffff;
  }
  * { box-sizing: border-box; margin: 0; padding: 0; }
  html, body {
    width: 1200px;
    height: 843px;
    overflow: hidden;
    background: var(--page-bg);
    font-family: "Arimo", Arial, sans-serif;
  }
  .canvas {
    position: relative;
    width: 1200px;
    height: 843px;
  }
  .card {
    position: absolute;
    top: 273px;
    width: 520px;
    height: 297px;
    overflow: hidden;
    box-shadow: 0 6px 18px rgba(0,0,0,0.18);
  }
  /* Back side */
  .card--back {
    left: 60px;
    background: linear-gradient(160deg, var(--brand-blue-light) 0%, var(--brand-blue) 50%, var(--brand-blue-deep) 100%);
  }
  .card--back .wordmark {
    position: absolute;
    left: 0; right: 0;
    top: 104px;
    text-align: center;
    color: var(--text-white);
    font-size: 64px;
    font-weight: 400;
    letter-spacing: 1px;
  }
  .card--back .back-url {
    position: absolute;
    left: 0; right: 0;
    top: 192px;
    text-align: center;
    color: var(--text-white);
    font-size: 11px;
    letter-spacing: 6px;
    opacity: 0.9;
  }
  /* Front side */
  .card--front {
    left: 620px;
    background: var(--card-white);
  }
  .card--front .bands {
    position: absolute;
    left: 0; top: 0;
    width: 520px;
    height: 297px;
  }
  .card--front .wordmark {
    position: absolute;
    left: 40px;
    top: 38px;
    color: var(--brand-blue);
    font-size: 68px;
    font-weight: 400;
    letter-spacing: 1px;
  }
  .person {
    position: absolute;
    left: 24px;
    top: 150px;
  }
  .person__name {
    color: var(--brand-blue);
    font-size: 17px;
    font-weight: 700;
    line-height: 1.1;
  }
  .person__title {
    color: var(--text-grey);
    font-size: 14px;
    line-height: 1.3;
  }
  .contact {
    position: absolute;
    right: 14px;
    top: 228px;
    list-style: none;
    color: var(--text-white);
    font-size: 13px;
  }
  .contact__item {
    display: flex;
    justify-content: flex-end;
    align-items: center;
    gap: 7px;
    height: 20px;
  }
  .contact__icon {
    width: 13px;
    height: 13px;
    flex: none;
  }
</style>
</head>
<body>
<main class="canvas">

  <section class="card card--back" aria-label="Card back">
    <div class="wordmark">quilmora</div>
    <div class="back-url">www.quilmora.com</div>
  </section>

  <section class="card card--front" aria-label="Card front">
    <svg class="bands" viewBox="0 0 520 297" aria-hidden="true">
      <polygon points="0,225 327,225 275,297 0,297" fill="var(--band-grey)"/>
      <polygon points="0,287 282,287 275,297 0,297" fill="var(--band-grey-light)"/>
      <polygon points="356,185 520,185 520,297 275,297" fill="var(--brand-blue)"/>
    </svg>

    <div class="wordmark">quilmora</div>

    <div class="person">
      <div class="person__name">Devin Holt</div>
      <div class="person__title">President</div>
    </div>

    <ul class="contact">
      <li class="contact__item">
        <span>(800) 471-2960</span>
        <svg class="contact__icon" viewBox="0 0 16 16" aria-hidden="true">
          <path d="M4 1.5 L6 1.5 L7 5 L5.3 6.2 C6 8 7.8 9.9 9.8 10.7 L11 9 L14.5 10 L14.5 12.2 C14.5 13.5 13.4 14.5 12 14.4 C6.4 13.8 2.2 9.6 1.6 4 C1.5 2.6 2.6 1.5 4 1.5 Z" fill="var(--text-white)"/>
        </svg>
      </li>
      <li class="contact__item">
        <span>sleep@quilmora.com</span>
        <svg class="contact__icon" viewBox="0 0 16 16" aria-hidden="true">
          <rect x="1" y="3" width="14" height="10" rx="1" fill="var(--text-white)"/>
          <path d="M1.5 3.5 L8 9 L14.5 3.5" fill="none" stroke="var(--brand-blue)" stroke-width="1.3"/>
        </svg>
      </li>
      <li class="contact__item">
        <span>www.quilmora.com</span>
        <svg class="contact__icon" viewBox="0 0 16 16" aria-hidden="true">
          <circle cx="8" cy="8" r="7" fill="var(--text-white)"/>
          <path d="M8 4.5 L11 8 L8 11.5 L5 8 Z" fill="var(--brand-blue)"/>
        </svg>
      </li>
    </ul>
  </section>

</main>
</body>
</html>
```